Business cards for a fun web development agency

Hi,I am building a web development agency. You can read about it on the website http://kite-loft.examplehost.com. Basically, I want to focus on free and open source products and stay as far away from the corporate business feeling as possible. I want to build a community so I want the business card to feel fun and approachable (at the risk of professional if need be). I am uploading some of my image assets in various file formats. Feel free to use them or make your own if you want just keeping in theme with the website.
Industry/Entity Type
Building
Contact Information for Business Card
Company Name: Boat ShedWebsite: www.kiteloftdev.example (it's currently in alpha on http://kite-loft.examplehost.com if you want to see the them we are trying to capture)My name is: Banner B. SchaferMy email: banner@boatsheddev.comMy phone: 0431 587 904
Look and feel

```html
<!DOCTYPE html>
<html lang="en">
<head>
<meta charset="utf-8">
<title>Kite Loft — Business Card</title>
<link rel="stylesheet" href="https://fonts.googleapis.com/css2?family=Questrial&family=Roboto+Condensed:wght@500;700&display=swap">
<style>
  :root {
    --page-bg: #e7e4df;
    --card-top: #f4f6f7;
    --card-bottom: #e3e7ea;
    --brand-blue: #2f9fd2;
    --band-blue: #36a3d4;
    --band-edge-dark: #1b2228;
    --band-edge-light: #c9ced2;
    --ink: #1f2a33;
    --white: #ffffff;
    --icon-disc: #c9d6de;
    --icon-glyph: #7f8e99;
    --footer-light: #eef0f2;
    --footer-mid: #b8bec3;
  }
  html, body {
    margin: 0;
    width: 1200px;
    height: 769px;
    overflow: hidden;
    background: var(--page-bg);
  }
  .business-card {
    position: absolute;
    left: 100px;
    top: 85px;
    width: 1000px;
    height: 600px;
    border-radius: 14px;
    background: linear-gradient(170deg, var(--card-top), var(--card-bottom));
    box-shadow: 0 18px 40px rgba(0,0,0,.18);
    overflow: hidden;
    font-family: "Questrial", sans-serif;
  }
  .brand {
    position: absolute;
    top: 108px;
    left: 0;
    width: 100%;
    text-align: center;
    font-size: 50px;
    letter-spacing: 1px;
    color: var(--brand-blue);
    text-transform: uppercase;
  }
  .info-band {
    position: absolute;
    top: 222px;
    left: 0;
    width: 100%;
    height: 254px;
    background: var(--band-blue);
    border-top: 6px solid var(--band-edge-dark);
    border-bottom: 6px solid var(--band-edge-dark);
    box-shadow: 0 -5px 0 var(--band-edge-light), 0 5px 0 var(--band-edge-light);
  }
  .info-column {
    position: absolute;
    top: 36px;
    width: 330px;
    margin-left: -165px;
    text-align: center;
    color: var(--white);
  }
  .info-column--person { left: 192px; }
  .info-column--web { left: 508px; }
  .info-column--phone { left: 812px; }
  .info-icon {
    display: block;
    margin: 0 auto 14px;
    width: 90px;
    height: 90px;
  }
  .person-name {
    font-family: "Roboto Condensed", sans-serif;
    font-weight: 700;
    font-size: 38px;
    line-height: 1;
    margin: 0;
    white-space: nowrap;
  }
  .person-role {
    font-family: "Roboto Condensed", sans-serif;
    font-weight: 500;
    font-size: 15px;
    letter-spacing: 1px;
    margin: 6px 0 0;
    text-transform: uppercase;
  }
  .contact-line {
    font-size: 26px;
    line-height: 1.15;
    margin: 0;
    letter-spacing: .5px;
    white-space: nowrap;
  }
  .social-footer {
    position: absolute;
    top: 482px;
    left: 0;
    width: 100%;
    height: 100px;
    background: linear-gradient(90deg, var(--footer-mid), var(--footer-light) 30%, var(--footer-light) 55%, var(--footer-mid) 100%);
    border-bottom: 4px solid var(--band-edge-dark);
  }
  .follow-label {
    position: absolute;
    left: 97px;
    top: 26px;
    color: var(--ink);
  }
  .follow-title {
    font-size: 28px;
    letter-spacing: 1px;
    margin: 0;
  }
  .follow-sub {
    font-size: 12px;
    letter-spacing: 1px;
    margin: 4px 0 0;
    text-transform: uppercase;
  }
  .social-marks {
    position: absolute;
    left: 336px;
    top: 33px;
    display: flex;
    gap: 40px;
  }
  .social-mark {
    width: 30px;
    height: 30px;
    border-radius: 4px;
    background: var(--ink);
  }
</style>
</head>
<body>
  <div class="business-card">
    <div class="brand">Kite Loft</div>

    <div class="info-band">
      <div class="info-column info-column--person">
        <svg class="info-icon" viewBox="0 0 90 90" aria-hidden="true">
          <circle cx="45" cy="45" r="44" fill="var(--white)"/>
          <circle cx="45" cy="45" r="37" fill="var(--icon-glyph)"/>
          <circle cx="45" cy="36" r="12" fill="var(--white)"/>
          <path d="M23 66 Q45 42 67 66 Z" fill="var(--white)"/>
        </svg>
        <p class="person-name">CORWIN T. ALDOUS</p>
        <p class="person-role">Founder &amp; Developer</p>
      </div>

      <div class="info-column info-column--web">
        <svg class="info-icon" viewBox="0 0 90 90" aria-hidden="true">
          <circle cx="45" cy="45" r="44" fill="var(--white)"/>
          <circle cx="45" cy="45" r="37" fill="var(--icon-disc)"/>
          <g fill="none" stroke="var(--icon-glyph)" stroke-width="3">
            <circle cx="45" cy="45" r="24"/>
            <ellipse cx="45" cy="45" rx="11" ry="24"/>
            <line x1="21" y1="45" x2="69" y2="45"/>
            <line x1="45" y1="21" x2="45" y2="69"/>
            <path d="M25 33 H65 M25 57 H65"/>
          </g>
        </svg>
        <p class="contact-line">corwin@kiteloftdev.example</p>
        <p class="contact-line">www.kiteloftdev.example</p>
      </div>

      <div class="info-column info-column--phone">
        <svg class="info-icon" viewBox="0 0 90 90" aria-hidden="true">
          <circle cx="45" cy="45" r="44" fill="var(--white)"/>
          <circle cx="45" cy="45" r="37" fill="var(--icon-disc)"/>
          <rect x="33" y="21" width="24" height="46" rx="4" fill="var(--icon-glyph)"/>
          <rect x="36" y="27" width="18" height="31" fill="var(--white)"/>
          <circle cx="45" cy="62" r="2.5" fill="var(--white)"/>
        </svg>
        <p class="contact-line">0431 587 904</p>
        <p class="contact-line">0431 587 904</p>
      </div>
    </div>

    <div class="social-footer">
      <div class="follow-label">
        <p class="follow-title">FOLLOW US</p>
        <p class="follow-sub">On social networks</p>
      </div>
      <div class="social-marks">
        <span class="social-mark"></span>
        <span class="social-mark"></span>
        <span class="social-mark"></span>
        <span class="social-mark"></span>
      </div>
    </div>
  </div>
</body>
</html>
```